Los Brava Dip – CPG Website with WordPress - Store Locator: WP Maps plugin

Larkfield Food Company is a startup consumer packaged goods (CPG) brand launching its flagship product line — Los Brava Dip. We’re seeking a talented web designer to create a bold, professional, mobile-optimized website using WordPress with a WP Maps store locator to help customers find local retailers.

Our goal is to build a strong online presence that supports both retail growth and direct-to-consumer sales.

See Los Brava _Website_Design_Brief word document.

The website URL is https://losbravadip.example/

Target Market(s)

Consumers of gourmet salsa

Industry/Entity Type

Consumer Packaged Goods - Salsa manufacturer.

Coding

Coded - Design and coding required

Number of Pages Required

5+ page

Requirements
Must have
• The design of the Los Brava Dip website shall emulate the clean, polished aesthetic of Fennigo.example.

```html
<!DOCTYPE html>
<html lang="en">
<head>
<meta charset="utf-8">
<title>Los Brava Dip – Home</title>
<link rel="stylesheet" href="https://fonts.googleapis.com/css2?family=Anton&family=Roboto:wght@400;500;700&display=swap">
<style>
:root{
  --red:#c8452a;
  --red-dark:#b63a22;
  --yellow:#f0b733;
  --black:#0b0b0b;
  --green:#3e6e22;
  --green-dark:#2f5a18;
  --white:#ffffff;
  --text:#222;
  --muted:#6a6a6a;
  --footer:#1c1c1c;
}
*{box-sizing:border-box;margin:0;padding:0}
html,body{width:1200px;height:3146px;overflow:hidden}
body{font-family:"Roboto",sans-serif;color:var(--text);background:var(--white);position:relative}
.display{font-family:"Anton",sans-serif;font-weight:400;letter-spacing:.5px}
section,header,footer,.promo-bar{position:absolute;left:0;width:1200px}

.promo-bar{top:0;height:40px;background:var(--red);color:var(--white);font-size:14px;font-weight:700;text-align:center;line-height:40px}

.site-header{top:40px;height:90px;background:var(--black)}
.brand{position:absolute;left:144px;top:26px;display:flex;align-items:center;gap:8px;color:var(--red);font-weight:700;font-size:26px}
.brand .dot{width:14px;height:14px;border-radius:50%;background:var(--red)}
.main-nav{position:absolute;left:412px;top:35px;display:flex;gap:32px}
.main-nav a{color:var(--white);text-decoration:none;font-size:15px;font-weight:700}
.main-nav a.active{color:var(--yellow)}
.cart{position:absolute;left:1020px;top:31px;width:28px;height:28px;border-radius:50%;background:var(--yellow);display:flex;align-items:center;justify-content:center}
.cart .count{position:absolute;top:-5px;right:-6px;width:14px;height:14px;border-radius:50%;background:var(--red);color:#fff;font-size:9px;text-align:center;line-height:14px}

.hero{top:130px;height:605px;background:radial-gradient(ellipse at 50% 30%,#5a4330 0%,#2b2019 45%,#120d0a 100%)}
.hero h1{position:absolute;top:85px;width:100%;text-align:center;color:var(--white);font-size:52px;line-height:57px}
.hero p{position:absolute;top:200px;width:100%;text-align:center;color:var(--white);font-size:19px}
.hero-actions{position:absolute;top:236px;left:428px;display:flex;gap:8px}
.btn{display:inline-flex;align-items:center;gap:12px;height:38px;padding:0 10px 0 21px;border-radius:19px;font-weight:700;font-size:15px;text-decoration:none;text-transform:uppercase}
.btn .arrow{width:22px;height:22px;border-radius:50%;background:var(--white);display:flex;align-items:center;justify-content:center}
.btn-red{background:var(--red);color:var(--white)}
.btn-yellow{background:var(--yellow);color:var(--black)}
.slide-arrow{position:absolute;top:317px;width:36px;height:36px;border-radius:50%;background:#3b3b3b;display:flex;align-items:center;justify-content:center}

.jars{position:absolute;left:265px;top:450px;width:670px;height:435px;border-radius:60px 60px 30px 30px;background:linear-gradient(90deg,#d9442a 0%,#e2633a 28%,#93b23c 40%,#a9c04a 58%,#ef8a2e 72%,#e9572b 100%);z-index:3}

.featured{top:735px;height:767px;background:var(--yellow)}
.section-title{position:absolute;width:100%;text-align:center;font-size:50px;line-height:60px;color:var(--red)}
.featured .section-title{top:220px}
.product-card{position:absolute;top:299px;width:286px;height:342px;background:var(--white);border-radius:16px;text-align:center}
.product-card.selected{border:2px solid var(--red);top:297px;width:290px;height:346px}
.product-card .tag{margin-top:22px;font-size:12px;color:var(--red);text-transform:uppercase}
.product-card .jar{margin:14px auto 0;width:108px;height:172px;border-radius:18px 18px 24px 24px}
.product-card h3{margin-top:24px;font-size:20px;font-weight:500}
.product-card p{margin:12px auto 0;width:220px;font-size:14px;color:var(--muted);line-height:20px}
.product-card .btn{position:absolute;left:56px;bottom:-20px;height:38px}
.card-arrow{position:absolute;top:466px}

.reviews{top:1502px;height:546px;background:radial-gradient(ellipse at 50% 40%,#4a7d2a 0%,var(--green) 55%,var(--green-dark) 100%)}
.reviews .section-title{top:80px;color:var(--white)}
.review-card{position:absolute;top:173px;width:426px;height:240px;background:var(--white);border-radius:18px;box-shadow:7px 7px 0 var(--yellow);padding:28px 30px}
.stars{display:flex;gap:4px}
.review-card h3{margin-top:14px;font-size:20px;color:var(--red);font-weight:500}
.review-card p{margin-top:14px;font-size:14px;line-height:24px;color:var(--muted)}
.dots{position:absolute;top:466px;left:571px;display:flex;gap:9px}
.dots span{width:13px;height:13px;border-radius:50%;background:#ddd}
.dots span.on{background:var(--red)}

.recipes{top:2048px;height:485px;background:var(--white)}
.recipes .section-title{top:22px}
.recipe-row{position:absolute;top:108px;left:0;display:flex}
.recipe{width:240px;height:377px;display:flex}
.recipe .photo{width:202px;height:100%}
.recipe .label{width:38px;background:var(--red);color:var(--white);writing-mode:vertical-rl;transform:rotate(180deg);display:flex;align-items:center;justify-content:center;font-size:14px;font-weight:700;text-transform:uppercase}

.social-follow{top:2533px;height:240px;background:var(--yellow)}
.social-follow .section-title{top:91px;font-size:52px;line-height:60px}
.rule{position:absolute;left:411px;width:378px;height:3px;background:var(--red)}

.site-footer{top:2773px;height:373px;background:linear-gradient(90deg,#161616,#2a2a2a 50%,#161616)}
.site-footer .brand{top:115px;left:144px}
.socials{position:absolute;left:144px;top:183px;display:flex;gap:9px}
.socials span{width:30px;height:30px;border-radius:50%;background:#2c2c2c;display:flex;align-items:center;justify-content:center}
.socials span.on{background:var(--red)}
.footer-col h4{font-size:18px;color:var(--red);font-weight:700;text-transform:uppercase}
.links{position:absolute;left:414px;top:85px}
.links ul{list-style:none;margin-top:8px}
.links li{color:#fff;font-size:14px;line-height:24px;padding-left:32px;position:relative}
.links li::before{content:"";position:absolute;left:4px;top:8px;width:9px;height:9px;border-radius:50%;background:var(--red)}
.newsletter{position:absolute;left:704px;top:85px}
.email{margin-top:14px;width:356px;height:48px;border:1px solid #777;border-radius:8px;display:flex;align-items:center;padding-left:20px;gap:16px;color:#fff;font-size:14px}
.newsletter .btn{margin-top:11px}
.copyright{position:absolute;top:320px;width:100%;text-align:center;color:#fff;font-size:14px}
</style>
</head>
<body>

<div class="promo-bar">AT $4.79 THAT IS A GREAT VALUE.</div>

<header class="site-header">
  <div class="brand"><span class="dot"></span>Los Brava</div>
  <nav class="main-nav">
    <a class="active" href="#">HOME</a><a href="#">PRODUCT</a><a href="#">WHERE TO BUY</a><a href="#">RECIPE</a><a href="#">ABOUT</a><a href="#">REVIEW</a>
  </nav>
  <div class="cart">
    <svg width="14" height="14" viewBox="0 0 14 14"><path d="M3 5h8l-1 8H4z M5 5V3.5a2 2 0 0 1 4 0V5" fill="none" stroke="#000" stroke-width="1.3"/></svg>
    <span class="count">0</span>
  </div>
</header>

<section class="hero" role="img" aria-label="Blurred warm restaurant background">
  <h1 class="display">BOLD FLAVOR. REAL INGREDIENTS.<br>NO COMPROMISES.</h1>
  <p>Taste the difference in every jar — handcrafted Texas salsa, made for purists.</p>
  <div class="hero-actions">
    <a class="btn btn-red" href="#">Shop Now <span class="arrow"><svg width="10" height="10" viewBox="0 0 10 10"><path d="M3 1l4 4-4 4" fill="none" stroke="#c8452a" stroke-width="1.6"/></svg></span></a>
    <a class="btn btn-yellow" href="#">Find in Stores <span class="arrow"><svg width="10" height="10" viewBox="0 0 10 10"><path d="M3 1l4 4-4 4" fill="none" stroke="#000" stroke-width="1.6"/></svg></span></a>
  </div>
  <div class="slide-arrow" style="left:53px"><svg width="12" height="12" viewBox="0 0 12 12"><path d="M8 1L3 6l5 5" fill="none" stroke="#fff" stroke-width="2"/></svg></div>
  <div class="slide-arrow" style="left:1109px"><svg width="12" height="12" viewBox="0 0 12 12"><path d="M4 1l5 5-5 5" fill="none" stroke="#fff" stroke-width="2"/></svg></div>
</section>

<div class="jars" role="img" aria-label="Three jars of Los Brava salsa: Habanero, Verde and All Natural"></div>

<section class="featured" role="region" aria-label="Featured products">
  <h2 class="section-title display">FEATURED PRODUCTS</h2>
  <svg class="card-arrow" style="left:70px" width="14" height="22" viewBox="0 0 14 22"><path d="M11 2L3 11l8 9" fill="none" stroke="#c8452a" stroke-width="3.5"/></svg>
  <div class="product-card" style="left:144px">
    <div class="tag">Classic &amp; Balanced</div>
    <div class="jar" role="img" aria-label="All Natural salsa jar" style="background:linear-gradient(#d7a53c,#e9822f 45%,#c94a2a)"></div>
    <h3>All Natural Salsa</h3>
    <p>Lorem ipsum dolor sit amet, cons ectetur adipiscing elit</p>
  </div>
  <div class="product-card selected" style="left:455px">
    <div class="tag">Hot with Depth</div>
    <div class="jar" role="img" aria-label="Habanero salsa jar" style="background:linear-gradient(#d7a53c,#d9452a 45%,#b73222)"></div>
    <h3>Habanero Salsa</h3>
    <p>Lorem ipsum dolor sit amet, cons ectetur adipiscing elit</p>
    <a class="btn btn-red" href="#">Add to Cart <span class="arrow"><svg width="10" height="10" viewBox="0 0 10 10"><path d="M3 1l4 4-4 4" fill="none" stroke="#c8452a" stroke-width="1.6"/></svg></span></a>
  </div>
  <div class="product-card" style="left:770px">
    <div class="tag">Fresh &amp; Zesty</div>
    <div class="jar" role="img" aria-label="Verde salsa jar" style="background:linear-gradient(#d7a53c,#8fb03a 45%,#6c8d2c)"></div>
    <h3>Verde Salsa</h3>
    <p>Lorem ipsum dolor sit amet, cons ectetur adipiscing elit</p>
  </div>
  <svg class="card-arrow" style="left:1120px" width="14" height="22" viewBox="0 0 14 22"><path d="M3 2l8 9-8 9" fill="none" stroke="#c8452a" stroke-width="3.5"/></svg>
</section>

<section class="reviews" role="region" aria-label="Customer reviews">
  <h2 class="section-title display">CUSTOMER REVIEWS</h2>
  <article class="review-card" style="left:144px">
    <div class="stars">
      <svg width="80" height="14" viewBox="0 0 80 14"><g fill="#f0b733"><path id="s" d="M7 0l2 4.5 5 .5-3.7 3.3 1 5L7 10.8 2.7 13.3l1-5L0 5l5-.5z"/><use href="#s" x="16"/><use href="#s" x="32"/><use href="#s" x="48"/><use href="#s" x="64"/></g></svg>
    </div>
    <h3>Very good, and I’m a salsa snob!</h3>
    <p>Lorem ipsum dolor sit amet, consectetur adipiscing elit, sed do eiusmod tempor incididunt ut labore et dolore ma gna aliqua. Ut enim ad minim veniam, quis nostrud exerci tation ullamco laboris nisi ut aliquip ex ea commodo consequat.</p>
  </article>
  <article class="review-card" style="left:630px">
    <div class="stars">
      <svg width="80" height="14" viewBox="0 0 80 14"><g fill="#f0b733"><use href="#s"/><use href="#s" x="16"/><use href="#s" x="32"/><use href="#s" x="48"/><use href="#s" x="64"/></g></svg>
    </div>
    <h3>Awesome taste, fresh.</h3>
    <p>Lorem ipsum dolor sit amet, consectetur adipiscing elit, sed do eiusmod tempor incididunt ut labore et dolore ma gna aliqua. Ut enim ad minim veniam, quis nostrud exerci tation ullamco laboris nisi ut aliquip ex ea commodo consequat.</p>
  </article>
  <div class="dots"><span></span><span class="on"></span><span></span></div>
</section>

<section class="recipes" role="region" aria-label="Recipes">
  <svg style="position:absolute;left:70px;top:50px" width="14" height="22" viewBox="0 0 14 22"><path d="M11 2L3 11l8 9" fill="none" stroke="#c8452a" stroke-width="3.5"/></svg>
  <h2 class="section-title display">MOST TASTY RECIPES</h2>
  <svg style="position:absolute;left:1120px;top:50px" width="14" height="22" viewBox="0 0 14 22"><path d="M3 2l8 9-8 9" fill="none" stroke="#c8452a" stroke-width="3.5"/></svg>
  <div class="recipe-row">
    <div class="recipe"><div class="photo" role="img" aria-label="Mexican beef and rice with melted cheese" style="background:linear-gradient(135deg,#8a3a1c,#c8642c,#6b2a14)"></div><div class="label">One Pot Mexican Beef and Rice</div></div>
    <div class="recipe"><div class="photo" role="img" aria-label="Black bean and salsa soup in teal bowls" style="background:linear-gradient(135deg,#3a6f6a,#5a2a2e,#2fa7b0)"></div><div class="label">Los Brava’s Black Bean and Salsa Soup</div></div>
    <div class="recipe"><div class="photo" role="img" aria-label="Baked chicken with salsa and sour cream on a blue plate" style="background:linear-gradient(135deg,#2a4a7a,#c9874a,#1e3560)"></div><div class="label">Baked Chicken with Salsa and Sour Cream</div></div>
    <div class="recipe"><div class="photo" role="img" aria-label="Oven-baked salsa chicken in a skillet" style="background:linear-gradient(135deg,#9a9690,#b8562c,#5a5650)"></div><div class="label">Zesty Oven-Baked Salsa Chicken</div></div>
    <div class="recipe"><div class="photo" role="img" aria-label="Salsa beef bowl with avocado and greens" style="background:linear-gradient(135deg,#d8d8d8,#6a9a3a,#2a2a2a)"></div><div class="label">Slow Cooker Salsa Beef</div></div>
  </div>
</section>

<section class="social-follow" role="region" aria-label="Follow us">
  <div class="rule" style="top:72px"></div>
  <h2 class="section-title display">FOLLOW LOS BRAVA’S ON SOCIAL</h2>
  <div class="rule" style="top:161px"></div>
</section>

<footer class="site-footer" role="contentinfo">
  <div class="brand"><span class="dot"></span>Los Brava</div>
  <div class="socials">
    <span><svg width="10" height="10"><circle cx="5" cy="5" r="3" fill="#fff"/></svg></span>
    <span class="on"><svg width="10" height="10"><circle cx="5" cy="5" r="3" fill="#fff"/></svg></span>
    <span><svg width="10" height="10"><circle cx="5" cy="5" r="3" fill="#fff"/></svg></span>
  </div>
  <div class="footer-col links">
    <h4>Quick Links</h4>
    <ul>
      <li>Contact Us</li><li>Frequently Asked Questions</li><li>Careers</li><li>Privacy Policy</li><li>Shipping Policy</li><li>Terms and Conditions</li>
    </ul>
  </div>
  <div class="footer-col newsletter">
    <h4>Subscribe to our Newsletter</h4>
    <div class="email"><svg width="14" height="10" viewBox="0 0 14 10"><rect width="14" height="10" rx="1" fill="#c8452a"/><path d="M0 1l7 5 7-5" fill="none" stroke="#1c1c1c" stroke-width="1.2"/></svg>Email address</div>
    <a class="btn btn-red" href="#">Subscribe <span class="arrow"><svg width="10" height="10" viewBox="0 0 10 10"><path d="M3 1l4 4-4 4" fill="none" stroke="#c8452a" stroke-width="1.6"/></svg></span></a>
  </div>
  <div class="copyright">© Copyrights 2025 | All Rights Reserved</div>
</footer>

</body>
</html>
```